VFX Company Business Card Design Project

The Kestrel Works is a decentralized Visual Effects Studio servicing the television and feature film industries.
Project Brief:
Take our logo that was previously designed on Pencil Harbor and make a double sided business card.
Requirements:
- Card MUST be double sided.
- Front of card MUST have the yellow part of our logo against the dark grey background.
- Back of card is completely up to the designer.
- Back of card must include the complete company logo.
Please follow these File Preparation guidelines:
http://printnook.ca/infopage?file=filetype_en&s=PrintNook_new&lang=en
Business

```html
<!DOCTYPE html>
<html lang="en">
<head>
<meta charset="utf-8">
<title>The Kestrel Works – Business Cards</title>
<link href="https://fonts.googleapis.com/css2?family=Josefin+Sans:wght@300;400;600&family=Arimo:wght@400;700&display=swap" rel="stylesheet">
<style>
  :root {
    --backdrop: #e9e6e2;
    --card-dark: #262626;
    --brand-yellow: #fcc52b;
    --mark-light: #eef2e6;
    --tagline-grey: #9aa3a6;
    --url-white: #f2f2f2;
    --ink: #1c1c1c;
    --ink-soft: #2e2e2e;
    --metal-light: #e4e4e4;
    --metal-mid: #a9a9a9;
    --metal-dark: #3a3a3a;
  }
  * { box-sizing: border-box; margin: 0; padding: 0; }
  html, body {
    width: 1200px; height: 727px; overflow: hidden;
    background: var(--backdrop);
  }
  .sheet { position: relative; width: 1200px; height: 727px; }

  .card {
    position: absolute; width: 524px; height: 298px;
    border-radius: 30px; background: var(--card-dark);
    box-shadow: 0 4px 10px rgba(0,0,0,0.25);
    overflow: hidden;
  }
  .card--front     { left: 68px;  top: 42px; }
  .card--details   { left: 630px; top: 50px;
    background: linear-gradient(100deg, var(--metal-light) 0%, var(--metal-mid) 45%, var(--metal-dark) 100%); }
  .card--lockup    { left: 65px;  top: 384px; }
  .card--wordmark  { left: 623px; top: 388px; }

  .brand-name {
    font-family: "Josefin Sans", sans-serif; font-weight: 600;
    white-space: nowrap; line-height: 1;
  }
  .brand-dot { display: inline-block; border-radius: 50%; background: var(--brand-yellow); }

  /* Front: yellow name on dark grey */
  .front-mark {
    position: absolute; left: 0; right: 0; top: 0; bottom: 0;
    display: flex; align-items: center; justify-content: center; gap: 18px;
  }
  .front-mark .brand-dot { width: 34px; height: 34px; }
  .front-mark .brand-name { color: var(--brand-yellow); font-size: 46px; }

  /* Metal details card */
  .details-mark { position: absolute; left: 60px; top: 58px; }
  .details-mark .brand-name { color: var(--ink-soft); font-size: 44px; }
  .tagline {
    font-family: "Josefin Sans", sans-serif; font-weight: 300;
    letter-spacing: 0.32em; text-transform: uppercase; color: var(--ink-soft);
    white-space: nowrap;
  }
  .details-mark .tagline { font-size: 21px; margin-top: 6px; margin-left: 86px; color: #444; }

  .contact {
    position: absolute; top: 192px; left: 0; width: 100%;
    font-family: "Arimo", sans-serif; color: var(--ink);
  }
  .contact__person {
    position: absolute; right: 285px; text-align: right;
    font-size: 13px; line-height: 20px;
    padding-right: 12px; border-right: 1px solid rgba(0,0,0,0.25);
  }
  .contact__name { font-size: 19px; font-weight: 700; line-height: 26px; }
  .contact__lines { position: absolute; left: 268px; top: 4px; font-size: 13px; line-height: 21px; }

  /* Lockup card */
  .lockup { position: absolute; left: 36px; top: 108px; display: flex; align-items: center; gap: 16px; }
  .lockup .brand-dot { width: 30px; height: 30px; }
  .lockup .brand-name { color: var(--mark-light); font-size: 36px; }
  .lockup .tagline { color: var(--tagline-grey); font-size: 15px; margin-top: 6px; margin-left: 48px; }

  /* Wordmark card */
  .wordmark { position: absolute; left: 0; right: 0; top: 100px; text-align: center; }
  .wordmark .brand-name { color: var(--mark-light); font-size: 50px; }
  .wordmark .tagline { color: var(--tagline-grey); font-size: 21px; margin-top: 12px; }

  .card__url {
    position: absolute; left: 0; right: 0; bottom: 26px; text-align: center;
    font-family: "Josefin Sans", sans-serif; font-weight: 400;
    font-size: 17px; letter-spacing: 0.2em; color: var(--url-white);
  }
</style>
</head>
<body>
<main class="sheet">

  <section class="card card--front" aria-label="Card front">
    <div class="front-mark">
      <span class="brand-dot"></span>
      <span class="brand-name">The Kestrel Works</span>
    </div>
  </section>

  <section class="card card--details" aria-label="Card back with contact details">
    <div class="details-mark">
      <div class="brand-name">The Kestrel Works</div>
      <div class="tagline">Virtual Studio</div>
    </div>
    <div class="contact">
      <div class="contact__person">
        <div class="contact__name">Your Name</div>
        <div>Title</div>
        <div>00, Complex name</div>
        <div>City, State 0042</div>
      </div>
      <div class="contact__lines">
        <div>p: 0123 456789</div>
        <div>f: 0123 456789</div>
        <div>e: info@kestrelworks.com</div>
        <div>w: www.kestrelworks.com</div>
      </div>
    </div>
  </section>

  <section class="card card--lockup" aria-label="Card back with full lockup">
    <div class="lockup">
      <span class="brand-dot"></span>
      <div>
        <div class="brand-name">The Kestrel Works</div>
        <div class="tagline">Virtual Studio</div>
      </div>
    </div>
    <div class="card__url">www.kestrelworks.com</div>
  </section>

  <section class="card card--wordmark" aria-label="Card back with wordmark">
    <div class="wordmark">
      <div class="brand-name">The Kestrel Works</div>
      <div class="tagline">Virtual Studio</div>
    </div>
    <div class="card__url">www.kestrelworks.com</div>
  </section>

</main>
</body>
</html>
```